RB Halden Electric Yard Sign

Looking to have a yard sign designed that we can place at projects we are working on. Most likely will be 18" H x 24" W but flexible that we can increase the size if necessary. It should include our logo, our phone # 609-555-0147, website rbhaldenelectric.example and slogan, Wired with Care, Powered by Precision. Colors should match our brand.

```html
<!DOCTYPE html>
<html lang="en">
<head>
<meta charset="utf-8">
<title>RB Halden Electric – Yard Sign</title>
<link rel="stylesheet" href="https://fonts.googleapis.com/css2?family=Lexend:wght@600;700&display=swap">
<style>
  :root {
    --brand-navy: #163463;
    --brand-red: #ec2227;
    --sign-white: #ffffff;
    --page-bg: #eeeeee;
  }
  * { margin: 0; padding: 0; box-sizing: border-box; }
  html, body {
    width: 1200px;
    height: 877px;
    overflow: hidden;
    background: var(--page-bg);
  }
  .yard-sign {
    position: relative;
    width: 1200px;
    height: 877px;
    background: var(--sign-white);
    font-family: "Lexend", "Helvetica Neue", Arial, sans-serif;
    overflow: hidden;
  }
  .sign-shapes {
    position: absolute;
    inset: 0;
    width: 100%;
    height: 100%;
  }
  .shape-navy { fill: var(--brand-navy); }
  .shape-red { fill: var(--brand-red); }

  .brand-lockup {
    position: absolute;
    left: 110px;
    width: 1000px;
    top: 150px;
    height: 150px;
    display: flex;
    align-items: center;
    justify-content: center;
    gap: 28px;
  }
  .brand-mark {
    width: 54px;
    height: 54px;
    background: var(--brand-navy);
    flex: none;
  }
  .brand-name {
    color: var(--brand-red);
    font-weight: 700;
    font-size: 76px;
    letter-spacing: 1px;
    line-height: 1;
    white-space: nowrap;
  }

  .slogan {
    position: absolute;
    left: 0;
    width: 1170px;
    top: 431px;
    height: 105px;
    display: flex;
    align-items: center;
    justify-content: center;
    color: var(--sign-white);
    font-weight: 700;
    font-size: 42px;
    white-space: nowrap;
  }

  .phone {
    position: absolute;
    left: 90px;
    width: 1010px;
    top: 582px;
    height: 150px;
    display: flex;
    align-items: center;
    justify-content: center;
    color: var(--brand-navy);
    font-weight: 700;
    font-size: 136px;
    letter-spacing: -1px;
    line-height: 1;
    white-space: nowrap;
  }

  .website {
    position: absolute;
    left: 0;
    width: 1110px;
    top: 764px;
    height: 113px;
    display: flex;
    align-items: center;
    justify-content: center;
    color: var(--sign-white);
    font-weight: 600;
    font-size: 44px;
    white-space: nowrap;
  }
</style>
</head>
<body>
  <main class="yard-sign">
    <svg class="sign-shapes" viewBox="0 0 723 502" preserveAspectRatio="none" aria-hidden="true">
      <polygon class="shape-navy" points="0,0 42,0 0,250"/>
      <polygon class="shape-red" points="42,0 62,0 22,250 0,250"/>
      <rect class="shape-red" x="0" y="247" width="705" height="60"/>
      <rect class="shape-navy" x="0" y="437" width="668" height="65"/>
      <polygon class="shape-red" points="718,148 723,148 723,178 681,502 658,502"/>
      <polygon class="shape-navy" points="723,178 723,502 681,502"/>
    </svg>

    <div class="brand-lockup">
      <span class="brand-mark"></span>
      <span class="brand-name">RB Halden Electric</span>
    </div>

    <p class="slogan">Wired with Care, Powered by Precision.</p>
    <p class="phone">609-555-0147</p>
    <p class="website">www.rbhaldenelectric.example</p>
  </main>
</body>
</html>
```